Bulldog themed background for Real Estate Purchase Letter

I need a phantom background or watermark on a standard 8 1/2" x 11" paper. I am going to put a letter over the background. I want a bulldog theme that is cute, funny and original. This letter is for a real estate project and we want to capture the person sub-consciously . Attached is my personal dogs. If you want to use them you can but not required. I have attached the letter that I am trying to emulate. I want bulldogs not horses.

Target Market(s)

45 years old and higher

Industry/Entity Type

Real Estate

Font styles to use
Serif
Sans Serif

Colors

Designer to choose colors to be used in the design.

Requirements
Must have
• fun, happiness, reassuring,
Should not have
• violence, negativity, unhappy

```html
<!DOCTYPE html>
<html lang="en">
<head>
<meta charset="utf-8">
<title>Real Estate Purchase Letter</title>
<link rel="stylesheet" href="https://fonts.googleapis.com/css2?family=Roboto:wght@400&family=Questrial&family=EB+Garamond:wght@500&display=swap">
<style>
  :root {
    --canvas-bg: #5c5c5c;
    --paper-base: #d8c8cb;
    --paper-light: #e6dcde;
    --photo-dark: #7a7377;
    --photo-mid: #a99ea2;
    --photo-red: #c9a9ae;
    --ink: #2b2b2b;
    --body-ink: #4a4446;
    --signature-blue: #1f4e8c;
    --phone-grey: #5e5a5c;
  }
  * { margin: 0; padding: 0; box-sizing: border-box; }
  html, body {
    width: 1024px; height: 1200px; overflow: hidden;
    background: var(--canvas-bg);
  }
  .letter {
    position: absolute; left: 94px; top: 17px;
    width: 835px; height: 1166px;
    background: var(--paper-base);
    overflow: hidden;
  }
  .letter-backdrop {
    position: absolute; inset: 0;
    background:
      radial-gradient(ellipse 30% 22% at 78% 22%, var(--photo-dark), transparent 70%),
      radial-gradient(ellipse 35% 25% at 55% 28%, var(--photo-mid), transparent 75%),
      radial-gradient(ellipse 28% 24% at 18% 38%, var(--paper-light), transparent 70%),
      radial-gradient(ellipse 40% 12% at 40% 4%, var(--photo-red), transparent 70%),
      radial-gradient(ellipse 30% 20% at 75% 45%, var(--photo-mid), transparent 75%),
      linear-gradient(180deg, var(--paper-light) 0%, var(--paper-base) 55%, var(--paper-base) 100%);
    opacity: 0.85;
  }
  .block { position: absolute; left: 78px; width: 674px; }
  .recipient, .agent-title, .closing-contact, .postscript {
    font-family: 'Roboto', Arial, sans-serif;
    color: var(--ink);
  }
  .recipient-name { top: 130px; font-size: 17px; }
  .recipient-address { top: 176px; font-size: 17px; line-height: 23px; }
  .agent-title {
    position: absolute; top: 150px; right: 83px;
    font-size: 16px;
  }
  .letter-body {
    font-family: 'Questrial', 'Century Gothic', sans-serif;
    color: var(--body-ink);
    font-size: 15px; line-height: 26.7px;
    text-align: justify; hyphens: auto;
  }
  .letter-body strong { color: var(--ink); font-weight: 700; }
  .salutation { top: 278px; }
  .para-intro { top: 331px; }
  .para-offer { top: 465px; }
  .para-invite { top: 625px; }
  .sign-off { top: 812px; }
  .signature-mark {
    position: absolute; left: 78px; top: 848px;
    width: 110px; height: 50px;
  }
  .signer-name {
    top: 908px;
    font-family: 'EB Garamond', Georgia, serif;
    font-weight: 500; font-size: 25px;
    color: var(--signature-blue);
  }
  .signer-phone {
    top: 948px;
    font-family: 'Roboto', Arial, sans-serif;
    font-size: 16px; color: var(--phone-grey);
  }
  .postscript { top: 998px; font-size: 16px; line-height: 27px; }
</style>
</head>
<body>
  <main class="letter">
    <div class="letter-backdrop" role="img" aria-label="Faded watermark photo of smiling bulldogs"></div>

    <p class="block recipient recipient-name">Mr Outta State Owner</p>
    <p class="block recipient recipient-address">12345 Maple Street,<br>BROOKFIELD FL 34000 1200</p>
    <p class="agent-title">Licensed Real estate agent</p>

    <p class="block letter-body salutation">Dear Home Owner</p>
    <p class="block letter-body para-intro">I am writing you because I am interested in purchasing your property located at <strong>123 NE Harbor Ave BROOKFIELD FL.</strong> I live nearby in Fairhaven and I Purchase properties throughout the state of Flordia. Currently I am working on projects in the neighborhood, which is how I learned of your property.</p>
    <p class="block letter-body para-offer">Please call me at . So i can tell you how we can buy your property quickly, with no hassles and most importantly, at a fair price. I purchase the house directly from you, so there are no real estate commissions or extr fees coming out of your pocket. Furthermore, I always make cash offers so you never have to worry about delays resulting from a buyer trying to quality for a morgage and wastingyour valuble time.</p>
    <p class="block letter-body para-invite">I'll be glad to personally tell you more about how we can work together. All calls are completely confidential and there is no obligation whatsoever. Even if you are not inteested in selling at this time call (999) 9999-9999. So i can help you with derermining the value of your property. You should also keep this letter for further reference. since things in life have a tendency to chagne unexpectedly. Thank you for your time and consideration and I look forward to speaking with you.</p>
    <p class="block letter-body sign-off">Sincerely,</p>

    <div class="signature-mark" role="img" aria-label="Handwritten signature" style="background: radial-gradient(ellipse 50% 30% at 45% 50%, rgba(31,78,140,0.25), transparent 75%);"></div>

    <p class="block signer-name">Dana Whitfield</p>
    <p class="block signer-phone">(999)9999-99999</p>
    <p class="block postscript">P.S. If you would like to e-mail me information and pictures of your property. please send them to DANA@homemail.example</p>
  </main>
</body>
</html>
```